Occasions chocolate packaging

We are looking for 7 packaging designs for bars of chocolate.

Each design needs to be different and we’re not looking for a consistent brand or branding message across the designs. Inspiration should come from gift/occasion cards. Fun, simple, bold, vibrant colours and eye catching, i.e. not vintage or just text.

The front of the packaging should have the main message on and is free of any branding. You don’t need to design the back, just simply allow the main background colour or design pattern to continue around.

These are the different designs we are after, I’ve added in some text for each to give you some guidance but feel free to play around with the message if it suits the design better.

1) Mum
‘The best mum’, ‘Best mum in the World’, ‘Number 1 Mum’

2) Dad
‘The Best Dad’, ‘Best Dad Ever’, ‘Number 1 Dad’, ‘You’re my hero Dad’

3) Husband
‘Best Husband in the World’, ‘Husband I Love You’, ‘Darling Husband’

4) Wife
‘Best Wife in the World’, ‘For my Wonderful Wife’, ‘My Beautiful Wife’

5) Congratulations
Simple one, just Congratulations

6) Thinking of you
Try and keep this neutral as it could be used for happy and sad situations.

7) Thank you
Keep this gender neutral.

Sides:
The sides need to have the following text:

FINE BELGIAN DARK CHOCOLATE
infused with Orange

Back:
The main colour of the front should continue all the way around, we will place a box with the contents and bar code on here ourselves so no need to do anything.

Dimensions:
Attached in the document, front of package is 85mm by 190mm.

The packaging is made from folded card, the first blank part is for gluing the back on to.

Reason: I'm extending the deadline as I've only received 1 design so far which has followed the brief. Although I do like it, I would like to see at least some competition...

```html
<!DOCTYPE html>
<html lang="en">
<head>
<meta charset="utf-8">
<title>Thinking of You – Chocolate Bar Wrapper</title>
<link rel="stylesheet" href="https://fonts.googleapis.com/css2?family=Cormorant+Garamond:wght@400&family=Open+Sans:wght@300&family=Allura&display=swap">
<style>
  :root {
    --wrapper-red: #ff2200;
    --fold-line: #ff5c40;
    --sun-yellow: #ffd800;
    --ink-white: #ffffff;
  }
  html, body {
    margin: 0;
    padding: 0;
    width: 1200px;
    height: 2170px;
    overflow: hidden;
    background: var(--wrapper-red);
  }
  .wrapper {
    display: block;
    width: 1200px;
    height: 2170px;
  }
  .wrapper-background { fill: var(--wrapper-red); }
  .fold-line { stroke: var(--fold-line); stroke-width: 2; }
  .side-title {
    font-family: "Cormorant Garamond", "Times New Roman", serif;
    font-weight: 400;
    font-size: 104px;
    fill: var(--ink-white);
  }
  .side-flavour {
    font-family: "Open Sans", Arial, sans-serif;
    font-weight: 300;
    font-size: 86px;
    fill: var(--ink-white);
  }
  .smiley-area { fill: var(--sun-yellow); }
  .greeting {
    font-family: "Allura", "Brush Script MT", cursive;
    font-size: 190px;
    fill: var(--ink-white);
  }
</style>
</head>
<body>
<svg class="wrapper" viewBox="0 0 1200 2170" width="1200" height="2170" xmlns="http://www.w3.org/2000/svg">
  <rect class="wrapper-background" x="0" y="0" width="1200" height="2170"/>

  <line class="fold-line" x1="113" y1="0" x2="113" y2="2170"/>
  <line class="fold-line" x1="1085" y1="0" x2="1085" y2="2170"/>

  <text class="side-title" transform="translate(102 2148) rotate(-90)" textLength="2124" lengthAdjust="spacingAndGlyphs">FINE BELGIAN DARK CHOCOLATE</text>

  <text class="side-flavour" transform="translate(1180 1437) rotate(-90)" textLength="700" lengthAdjust="spacingAndGlyphs">infused with orange</text>

  <circle class="smiley-area" cx="592" cy="957" r="423" role="img" aria-label="Smiling face with closed eyes illustration"/>

  <g class="greeting-lines">
    <text class="greeting" transform="translate(440 1750) rotate(-29)" textLength="560" lengthAdjust="spacingAndGlyphs">Thinking</text>
    <text class="greeting" transform="translate(715 1845) rotate(-29)">of</text>
    <text class="greeting" transform="translate(815 2030) rotate(-29)">you</text>
  </g>
</svg>
</body>
</html>
```